Push notification screens at app start up

We have an existing news publication app platform and are adding categories to push notifications.

We need two screens designed (each for Zorbel, Quillet and Android for a total of 6d) that show when the app is first launched.

The workflow of our app:
0. app launch screen while webservices run (no work needed)
1. information screen to the user promoting the benefits of push notification with "Next" button. (see concept attached)
2. Push categories selection screen. This will have list of category types, with on/off switch.

"Select the categories that you wish to receive occasional notices:
Breaking News (on/off switch)
Local News (on/off switch)
Sports (on/off switch)
Local Events (on/off switch)
Weather Alerts (on/off switch)
Local Deals (on/off switch)"

"Enable these categories on the next screen."
"Next" button

Background:
When I was looking around at app designs, I came across this one (http://www.plinthworks.example/design/7719034) and I really liked it. We obviously have different features on our screen, but I’d like to have this same feel. The colors used in this design are perfect.

UPDATE: I do not mean to limit your design to match the layout as the one mentioned above. Please use your creativity for the layout.

Our standard font in Helvetica Neue.

Notes:
- our app is developed for all phone devices from Zorbel 4 to Zorbel 6, so designs should be thoughtful of vertical scrolling if needed.
- our app is developed for Quillets, so we'll need designs completed as well. (We can finalize Zorbel design first, then translate the design to Quillet.)
- our app is developed for Android phones (not tablets), so we'll need designs completed as well. (We can finalize iOS design first, then translater to Android UI design guidelines).

We hope to establish a good on-going relationship with the designer for as-needed work in the future.

News

• Helvetica Neue

• Clean designs. No clutter.
• We would likely go with the standard on/off switches for both iOS and Android, but are open to small custom variations.

```html
<!DOCTYPE html>
<html lang="en">
<head>
<meta charset="utf-8">
<title>Notifications – Onboarding Screen</title>
<link rel="stylesheet" href="https://fonts.googleapis.com/css2?family=Roboto:wght@300;400;500&display=swap">
<style>
  :root {
    --screen-bg: #000000;
    --chrome: #2c2c2e;
    --chrome-edge: #3a3a3d;
    --accent: #1f8fd8;
    --accent-text: #2b9ae2;
    --status-text: #e6e6e6;
  }
  * { box-sizing: border-box; margin: 0; padding: 0; }
  html, body {
    width: 1200px;
    height: 2352px;
    overflow: hidden;
    background: var(--screen-bg);
  }
  body {
    font-family: "Roboto", "Helvetica Neue", Arial, sans-serif;
    position: relative;
  }
  .status-bar {
    position: absolute;
    top: 0; left: 0;
    width: 1200px;
    height: 70px;
    background: var(--chrome);
    color: var(--status-text);
    font-size: 34px;
    font-weight: 400;
    display: flex;
    align-items: center;
    justify-content: space-between;
    padding: 0 22px;
  }
  .status-left, .status-right { display: flex; align-items: center; gap: 12px; }
  .status-time {
    position: absolute;
    left: 0; right: 0;
    text-align: center;
    font-weight: 500;
  }
  .signal { display: flex; gap: 5px; }
  .signal span {
    width: 15px; height: 15px; border-radius: 50%;
    border: 2px solid var(--status-text);
  }
  .signal span.on { background: var(--status-text); }

  .header-tab {
    position: absolute;
    top: 68px;
    left: 425px;
    width: 350px;
    height: 200px;
    background: var(--chrome);
    border-radius: 0 0 175px 175px / 0 0 130px 130px;
    display: flex;
    align-items: center;
    justify-content: center;
    padding-bottom: 20px;
  }
  .header-tab svg { width: 120px; height: 120px; }

  .intro {
    position: absolute;
    top: 560px;
    left: 120px;
    width: 960px;
    text-align: center;
    color: var(--accent-text);
  }
  .intro-title {
    font-size: 58px;
    font-weight: 400;
    letter-spacing: 1px;
    margin-bottom: 60px;
  }
  .intro-copy {
    font-size: 48px;
    font-weight: 300;
    line-height: 62px;
    margin-bottom: 60px;
  }

  .next-bar {
    position: absolute;
    left: 0; bottom: 0;
    width: 1200px;
    height: 170px;
    background: var(--chrome);
    border-top: 2px solid var(--chrome-edge);
    display: flex;
    align-items: center;
    justify-content: center;
    color: var(--accent);
    font-size: 52px;
    font-weight: 400;
    letter-spacing: 2px;
    gap: 20px;
  }
  .next-bar svg { width: 26px; height: 44px; }
</style>
</head>
<body>
  <header class="status-bar">
    <div class="status-left">
      <div class="signal"><span class="on"></span><span class="on"></span><span class="on"></span><span></span><span></span></div>
      <span class="carrier">KESTREL</span>
      <svg width="40" height="30" viewBox="0 0 40 30" aria-hidden="true">
        <path d="M4 10 A24 24 0 0 1 36 10" fill="none" stroke="#e6e6e6" stroke-width="4"/>
        <path d="M10 17 A15 15 0 0 1 30 17" fill="none" stroke="#e6e6e6" stroke-width="4"/>
        <circle cx="20" cy="25" r="4" fill="#e6e6e6"/>
      </svg>
    </div>
    <span class="status-time">4:21 PM</span>
    <div class="status-right">
      <svg width="20" height="34" viewBox="0 0 20 34" aria-hidden="true">
        <path d="M3 9 L16 24 L10 30 L10 4 L16 10 L3 25" fill="none" stroke="#e6e6e6" stroke-width="3"/>
      </svg>
      <span>100%</span>
      <svg width="60" height="28" viewBox="0 0 60 28" aria-hidden="true">
        <rect x="1.5" y="1.5" width="50" height="25" rx="4" fill="none" stroke="#e6e6e6" stroke-width="3"/>
        <rect x="6" y="6" width="41" height="16" rx="2" fill="#e6e6e6"/>
        <rect x="54" y="9" width="4" height="10" rx="1" fill="#e6e6e6"/>
      </svg>
    </div>
  </header>

  <div class="header-tab">
    <svg viewBox="0 0 100 100" aria-hidden="true">
      <g fill="none" stroke="#1f8fd8" stroke-width="5" stroke-linejoin="round" stroke-linecap="round">
        <path d="M18 40 H34 L54 24 V76 L34 60 H18 Z"/>
        <path d="M64 38 Q72 50 64 62"/>
        <path d="M72 30 Q86 50 72 70"/>
        <path d="M16 86 L84 14"/>
      </g>
    </svg>
  </div>

  <main class="intro">
    <h1 class="intro-title">NOTIFICATIONS</h1>
    <p class="intro-copy">By enabling push notifications, you can keep you up to date with occasional notifications related to items you care about. Select the categories on the next screen and then authorize the push noticifcations.</p>
    <p class="intro-copy">If you ever change your mind, you can adjust these options in the Settings menu of this app.</p>
  </main>

  <footer class="next-bar">
    <span>NEXT</span>
    <svg viewBox="0 0 26 44" aria-hidden="true">
      <path d="M4 4 L22 22 L4 40" fill="none" stroke="#1f8fd8" stroke-width="4"/>
    </svg>
  </footer>
</body>
</html>
```